RW Holloway LLC Business Card - Civil Engineering & Consulting Firm

We need a Business Card that is elegant, and masculine.  It is our Professional Civil Engineering & Consulting Company located in San Antonio TX (Not s construction or builder firm- no gears & no tool images please). We provide civil engineering services including  commercial site plans, grading and drainage plans, utility plans, hydraulics and hydrology, land planning, utility coordination, and other general civil engineering services related to commercial and residential development.
We have 2 existing Logos. We would like to convey reliability, strength, trustworthiness and attention to detail.  Blues and orange tones as per logo We are OK with the use of a darker blue in the mix.  We have 2 logo versions - Full Company Name Logo to go on the back of card, & Small Icon Logo for the front w/ personal Info.

Target Market(s)
Architects, Real Estate Developers, Other Strctural Engineers, Surveyers, General Contractors
Industry/Entity Type
Professional Civil Engineering
Contact Information for Business Card
Name, Position, Address, Cell & Office #, email, and company website
Font styles to use
Other font styles liked:
- Avian
Requirements
Should not have
- No Tools, No Gears, no Cranes, or Construction Equipment.

```html
<!DOCTYPE html>
<html lang="en">
<head>
<meta charset="utf-8">
<title>RW Holloway LLC Business Card</title>
<link rel="stylesheet" href="https://fonts.googleapis.com/css2?family=Montserrat:wght@400;500;700&family=Josefin+Sans:wght@300;400&display=swap">
<style>
  :root {
    --bg: #3a3a3b;
    --card: #1b1b1c;
    --card-back: #161617;
    --blue: #6fa3d8;
    --orange: #f2962a;
    --white: #f1f1f1;
    --rule: #55606e;
  }
  * { margin: 0; padding: 0; box-sizing: border-box; }
  html, body { width: 1200px; height: 801px; overflow: hidden; }
  body {
    background: var(--bg);
    font-family: "Montserrat", sans-serif;
    display: flex;
    align-items: center;
    justify-content: center;
    gap: 40px;
  }
  .card {
    position: relative;
    width: 540px;
    height: 309px;
    overflow: hidden;
  }
  .card--front { background: var(--card); }
  .card--back { background: var(--card-back); border-bottom: 4px solid var(--blue); }

  .edge-band {
    position: absolute;
    left: 0; right: 0; bottom: 0;
    height: 7px;
    display: flex;
  }
  .edge-band__blue { flex: 0 0 52%; background: var(--blue); }
  .edge-band__orange { flex: 1; background: var(--orange); }

  .brand {
    position: absolute;
    left: 36px;
    top: 118px;
    width: 220px;
  }
  .brand__name {
    font-family: "Josefin Sans", sans-serif;
    font-weight: 300;
    font-size: 27px;
    letter-spacing: 1px;
    color: var(--blue);
    white-space: nowrap;
    line-height: 1;
  }
  .brand__rule {
    height: 1px;
    background: var(--blue);
    margin: 8px 0 6px;
    opacity: .7;
  }
  .brand__tagline {
    font-family: "Josefin Sans", sans-serif;
    font-size: 9px;
    letter-spacing: 3.6px;
    color: var(--orange);
  }

  .divider {
    position: absolute;
    left: 272px;
    top: 50px;
    width: 1px;
    height: 200px;
    background: var(--rule);
  }

  .contact {
    position: absolute;
    left: 292px;
    top: 52px;
    color: var(--white);
  }
  .contact__name {
    font-weight: 700;
    font-size: 17px;
    color: var(--blue);
    letter-spacing: .3px;
  }
  .contact__title { font-size: 11px; margin-top: 2px; }
  .contact__address { font-size: 11px; line-height: 1.45; margin-top: 12px; }
  .contact__list { list-style: none; margin-top: 12px; font-size: 11px; line-height: 1.75; }
  .contact__list li { display: flex; align-items: center; gap: 8px; }
  .contact__icon { width: 10px; height: 10px; flex: none; }

  .back-pattern {
    position: absolute;
    inset: 0;
    background: linear-gradient(135deg, #121213 0%, #1f1f20 55%, #2a2a2b 100%);
  }
  .back-brand {
    position: absolute;
    left: 50%;
    top: 50%;
    transform: translate(-50%, -50%);
    display: flex;
    align-items: center;
    gap: 8px;
    font-weight: 500;
    font-size: 13px;
    color: var(--blue);
    white-space: nowrap;
  }
  .back-brand__mark { width: 8px; height: 8px; background: var(--orange); }
</style>
</head>
<body>
  <section class="card card--front">
    <div class="brand">
      <div class="brand__name">RW Holloway LLC</div>
      <div class="brand__rule"></div>
      <div class="brand__tagline">CONSULTING ENGINEERS</div>
    </div>

    <div class="divider"></div>

    <div class="contact">
      <div class="contact__name">DANIEL REYES</div>
      <div class="contact__title">President</div>
      <div class="contact__address">1830 Harbor View Drive<br>San Antonio TX 78205</div>
      <ul class="contact__list">
        <li>
          <svg class="contact__icon" viewBox="0 0 10 10"><rect x="2.5" y="0.5" width="5" height="9" rx="1" fill="none" stroke="var(--orange)" stroke-width="1.2"/></svg>
          210-555-0143
        </li>
        <li>
          <svg class="contact__icon" viewBox="0 0 10 10"><path d="M2 1 L4 1 L4.6 3.2 L3.4 4.2 Q4.6 6 5.8 6.6 L6.8 5.4 L9 6 L9 8 Q5 9 1.5 5 Q1 3 2 1Z" fill="var(--orange)"/></svg>
          210-555-0178
        </li>
        <li>
          <svg class="contact__icon" viewBox="0 0 10 10"><rect x="0.5" y="2" width="9" height="6" fill="var(--orange)"/><path d="M0.5 2 L5 5.5 L9.5 2" fill="none" stroke="var(--card)" stroke-width="1"/></svg>
          info@rwhollowayconsulting.com
        </li>
        <li>
          <svg class="contact__icon" viewBox="0 0 10 10"><circle cx="5" cy="5" r="4.5" fill="var(--orange)"/><path d="M0.5 5 H9.5 M5 0.5 V9.5" stroke="var(--card)" stroke-width=".8"/></svg>
          www.rwhollowayconsulting.com
        </li>
      </ul>
    </div>

    <div class="edge-band">
      <div class="edge-band__blue"></div>
      <div class="edge-band__orange"></div>
    </div>
  </section>

  <section class="card card--back">
    <div class="back-pattern" role="img" aria-label="Subtle tone-on-tone repeating company monogram pattern across the card back"></div>
    <div class="back-brand">
      <span class="back-brand__mark"></span>
      RW Holloway LLC
    </div>
  </section>
</body>
</html>
```